Transport & Storage Company needs a revamp of current card

Would like to keep same colours & basic design but would like to "sharpen" up look of card.

Please remove "The Brisk Haulers"

Please add 1800 418 239 on front & back of card

Please add email address on back of card - colin@bluegatefreight.com.au

I would like our ABN No - 38 214 906 731 on back of card (which currently has logo only). Logo on back of card can be removed if insufficient space.

Please design another card (same as above) but with Maren Ashcombe - 0431 702 548, maren@bluegatefreight.com.au

I do not want cards to look "too busy" so please re-arrange layout of card if necessary.

Target Market(s)

Transport & Storage

Industry/Entity Type

It Company

Contact Information for Business Card

Please refer to attached current business card

Font styles to use
Other font styles liked:
• Tahoma

Requirements
Must have
• Refer to project decsription
Nice to have
Should not have

```html
<!DOCTYPE html>
<html lang="en">
<head>
<meta charset="utf-8">
<title>Bluegate Freight – Business Cards</title>
<link rel="stylesheet" href="https://fonts.googleapis.com/css2?family=Open+Sans:wght@400;700&display=swap">
<style>
  :root {
    --purple: #7b3f98;
    --grey: #58585a;
    --ink: #2b2b2b;
    --paper: #ffffff;
    --backdrop: #e6e6e8;
  }
  html, body {
    margin: 0;
    padding: 0;
    width: 1200px;
    height: 892px;
    overflow: hidden;
    background: var(--backdrop);
    font-family: "Open Sans", Tahoma, sans-serif;
  }
  .canvas {
    position: relative;
    width: 1200px;
    height: 892px;
  }
  .card {
    position: absolute;
    width: 540px;
    height: 330px;
    background: var(--paper);
    overflow: hidden;
    box-shadow: 0 4px 14px rgba(0,0,0,0.18);
  }
  .row--colin .card { top: 96px; }
  .row--maren .card { top: 466px; }
  .card--front { left: 40px; }
  .card--back  { left: 620px; }
  .card__bands {
    position: absolute;
    inset: 0;
    width: 540px;
    height: 330px;
  }
  .band--purple { fill: var(--purple); }
  .band--grey   { fill: var(--grey); }

  .brand-name {
    position: absolute;
    margin: 0;
    font-weight: 700;
    color: var(--purple);
    letter-spacing: 0.2px;
    white-space: nowrap;
  }
  .card--front .brand-name {
    top: 38px;
    left: 190px;
    font-size: 30px;
  }
  .person-name {
    position: absolute;
    top: 112px;
    left: 190px;
    margin: 0;
    font-size: 22px;
    font-weight: 700;
    color: var(--purple);
    white-space: nowrap;
  }
  .contact {
    position: absolute;
    margin: 0;
    font-size: 17px;
    line-height: 1.35;
    color: var(--ink);
    white-space: nowrap;
  }
  .contact--phones {
    left: 190px;
    top: 170px;
  }
  .contact--email {
    left: 190px;
    top: 236px;
  }

  .card--back .brand-name {
    top: 48px;
    left: 70px;
    font-size: 34px;
  }
  .back-details {
    position: absolute;
    top: 118px;
    left: 72px;
    margin: 0;
    font-size: 17px;
    line-height: 1.5;
    color: var(--purple);
    white-space: nowrap;
  }
</style>
</head>
<body>
<main class="canvas">

  <div class="card-set row--colin">
    <section class="card card--front" aria-label="Business card front, Colin Marsh">
      <svg class="card__bands" viewBox="0 0 540 330" aria-hidden="true">
        <polygon class="band--purple" points="0,0 20,0 95,330 0,330"/>
        <polygon class="band--grey" points="38,0 62,0 145,330 112,330"/>
        <polygon class="band--grey" points="540,200 540,330 440,330"/>
      </svg>
      <h1 class="brand-name">Bluegate Freight</h1>
      <h2 class="person-name">Colin Marsh</h2>
      <p class="contact contact--phones">0417 356 280<br>1800 418 239</p>
      <p class="contact contact--email">colin@bluegatefreight.com.au</p>
    </section>

    <section class="card card--back" aria-label="Business card back, Colin Marsh">
      <svg class="card__bands" viewBox="0 0 540 330" aria-hidden="true">
        <polygon class="band--grey" points="440,0 468,0 540,250 540,300"/>
        <polygon class="band--purple" points="488,0 540,0 540,185"/>
      </svg>
      <h2 class="brand-name">Bluegate Freight</h2>
      <p class="back-details">1800 418 239<br>colin@bluegatefreight.com.au<br>ABN 38 214 906 731<br>www.bluegatefreight.com.au</p>
    </section>
  </div>

  <div class="card-set row--maren">
    <section class="card card--front" aria-label="Business card front, Maren Ashcombe">
      <svg class="card__bands" viewBox="0 0 540 330" aria-hidden="true">
        <polygon class="band--purple" points="0,0 20,0 95,330 0,330"/>
        <polygon class="band--grey" points="38,0 62,0 145,330 112,330"/>
        <polygon class="band--grey" points="540,200 540,330 440,330"/>
      </svg>
      <h2 class="brand-name">Bluegate Freight</h2>
      <h2 class="person-name">Maren Ashcombe</h2>
      <p class="contact contact--phones">0431 702 548<br>1800 418 239</p>
      <p class="contact contact--email">maren@bluegatefreight.com.au</p>
    </section>

    <section class="card card--back" aria-label="Business card back, Maren Ashcombe">
      <svg class="card__bands" viewBox="0 0 540 330" aria-hidden="true">
        <polygon class="band--grey" points="440,0 468,0 540,250 540,300"/>
        <polygon class="band--purple" points="488,0 540,0 540,185"/>
      </svg>
      <h2 class="brand-name">Bluegate Freight</h2>
      <p class="back-details">1800 418 239<br>maren@bluegatefreight.com.au<br>ABN 38 214 906 731<br>www.bluegatefreight.com.au</p>
    </section>
  </div>

</main>
</body>
</html>
```